Velmar Radio Web

Radio Station web site to include but not limited:

- About US (company profile)
- Now playing (from our streaming server link)
- Upcoming events with a possibility to have photos for advertisement purpose, etc...
- Language switch from Russian to English

- Member section:
Login module (with new user name and password, forgot password, etc...)
Login module with Chatterloop details
Request a song
LIKE feature with Chatterloop...

- Social links: (along with Chatterloop LIKE)
Send page to a friend
share / chatterloop share
Chat section where all logged users can chat in the same room.

- Contact us (Radio email ID )
- iPAD - iPOD compatible

2 Websites were found to match the design that we re looking for:
http://www.trenivak.com and
http://carlosmendrutt.com

The site colors shall be matching and ongoing with our logo colors and designs as well.

Thanks,
Velmar Radio Team
Updates

Extended dead line and project is guaranteed.

Project Deadline Extended
Reason: Need more designs for review...

Industry/Entity Type

Radio

Requirements
Must have
• Chatterloop Login
Chatterloop LIKE
Users Chat Section
Language Switch
iPAD - iPOD compatible
Nice to have
• Less pages switch. Initial shall be to switch from russian to english (or EN to RU) but the less pages we flip, the better. (except pop ups for log in, request a song, etc...)

```html
<!DOCTYPE html>
<html lang="en">
<head>
<meta charset="utf-8">
<title>Velmar Radio</title>
<link rel="stylesheet" href="https://fonts.googleapis.com/css2?family=Ubuntu:wght@300;400;500&family=Arimo:wght@400;700&display=swap">
<style>
:root{
  --blue-deep:#0b3a78;
  --blue-mid:#1c5fae;
  --blue-light:#3c86d6;
  --panel:#0d3b78;
  --panel-dark:#082a5a;
  --heading:#2d5f93;
  --accent-light:#6fb1ee;
  --orange:#f5a623;
  --white:#ffffff;
  --grey-band:#a7a7a7;
  --text:#4d4d4d;
  --ui:"Ubuntu",sans-serif;
  --body:"Arimo",sans-serif;
}
*{box-sizing:border-box;margin:0;padding:0}
html,body{width:1143px;height:1200px;overflow:hidden;background:var(--white)}
.page{position:relative;width:1143px;height:1200px;font-family:var(--body);color:var(--text)}
.abs{position:absolute}

/* header */
.header{left:0;top:0;width:1143px;height:205px;background:radial-gradient(ellipse at 70% 0%,#3f86cf 0%,#1c5fae 45%,#0b3a78 100%)}
.mic{left:250px;top:10px;width:210px;height:195px;border-radius:40% 40% 0 0;background:linear-gradient(135deg,#f2f2f2,#9aa3ad 60%,#5d6670)}
.logo{left:150px;top:40px;width:136px;height:136px;border-radius:50%;background:var(--blue-deep);display:flex;align-items:center;justify-content:center;font-family:var(--ui);font-weight:500;font-size:17px;color:var(--white);text-align:center;line-height:1.1}
.wordmark{right:32px;top:40px;font-family:var(--ui);font-weight:300;font-size:44px;color:var(--white);letter-spacing:1px}
.lang-label{left:885px;top:133px;font-family:var(--ui);font-size:13px;color:var(--white)}
.lang-select{left:952px;top:132px;width:129px;height:21px;background:var(--white)}
.lang-select svg{position:absolute;right:8px;top:6px}

/* nav */
.nav{left:0;top:205px;width:1143px;height:44px;background:linear-gradient(#3a7fd0,#1e5fb2 55%,#174f98)}
.nav a{position:absolute;top:0;height:44px;line-height:43px;font-family:var(--ui);font-size:17px;color:var(--white);text-decoration:none;transform:translateX(-50%)}
.nav .active{left:105px;width:113px;transform:none;text-align:center;background:linear-gradient(#4a4a4a,#1a1a1a)}

/* hero */
.hero{left:0;top:249px;width:1143px;height:456px;background:radial-gradient(ellipse at 50% 40%,#2f7ad0 0%,#1a5aa8 50%,#0d3d7c 100%)}
.floor{left:0;top:590px}
.slide-side{background:linear-gradient(90deg,#e9e9e9,#2a2a2a 25%,#0d0d0d 70%,#cfcfcf)}
.slide-far-left{left:170px;top:355px;width:48px;height:251px;background:linear-gradient(#e8f2dc,#6bb43a 60%,#1a3b10)}
.slide-left{left:217px;top:307px;width:82px;height:331px}
.slide-right{left:829px;top:307px;width:82px;height:331px}
.slide-far-right{left:911px;top:355px;width:46px;height:251px;background:linear-gradient(90deg,#ffffff,#d9d9d9)}
.slide-main{left:298px;top:261px;width:531px;height:424px;background:radial-gradient(ellipse at 50% 45%,#a9a9a9 0%,#4a4a4a 55%,#1b1b1b 100%)}
.arrow{top:455px}

/* panels */
.panel{background:linear-gradient(#0d3b78,#0a3168 70%,#123f80);border-radius:6px}
.panel-tab{height:10px;border-radius:6px 6px 0 0;background:var(--blue-mid)}
.login{left:8px;top:727px;width:263px;height:309px}
.login-tab{left:22px;top:720px;width:235px}
.login h2{position:absolute;left:0;width:100%;top:10px;text-align:center;font-family:var(--ui);font-weight:400;font-size:22px;color:var(--accent-light)}
.field-label{position:absolute;left:23px;font-family:var(--ui);font-size:14px;color:#dfe9f5}
.field{position:absolute;left:19px;width:223px;height:29px;border:1px solid #3f6ea8;border-radius:7px;background:#0a2f63}
.sign-in{position:absolute;left:63px;top:212px;width:124px;height:28px;border-radius:5px;background:linear-gradient(#8a8a8a,#3c3c3c 50%,#262626);font-family:var(--ui);font-size:19px;color:var(--white);text-align:center;line-height:27px}
.forgot{position:absolute;left:0;width:100%;top:263px;text-align:center;font-family:var(--ui);font-size:14px;color:var(--orange)}

.section-title{font-family:var(--ui);font-weight:300;font-size:25px;color:var(--heading)}
.player{left:286px;top:773px;width:283px;height:217px;border-radius:6px;background:#0b0b0b}
.player-screen{position:absolute;left:10px;top:30px;width:263px;height:170px;border-radius:6px;background:radial-gradient(ellipse at 50% 35%,#5b5b5b,#1e1e1e 55%,#0c0c0c)}
.player-title{position:absolute;left:0;width:100%;top:34px;text-align:center;font-size:9px;color:#e6e6e6}
.player-foot{position:absolute;left:0;width:100%;top:149px;text-align:center;font-size:7px;color:#d8d8d8}
.player-bar{left:286px;top:992px;width:283px;height:16px}

.event{left:583px;width:270px;height:64px}
.event-thumb{position:absolute;left:0;top:0;width:74px;height:64px;border:2px solid #1843a8;background:linear-gradient(135deg,#1b4fe0,#6a87c9 50%,#e8e1d8)}
.event-name{position:absolute;left:81px;top:8px;font-size:12px;color:#111}
.event-more{position:absolute;left:225px;top:9px;font-size:11px;font-weight:700;color:#222;text-decoration:underline}
.event-text{position:absolute;left:80px;top:29px;width:190px;font-size:11px;line-height:20px;color:#555}

.contact{left:872px;top:727px;width:263px;height:309px}
.contact-tab{left:886px;top:720px;width:235px}
.contact h3{position:absolute;left:34px;font-family:var(--body);font-weight:400;font-size:14px;color:var(--accent-light)}
.contact-row{position:absolute;left:34px;display:flex;align-items:center;gap:12px;font-size:13px;color:#e9eef6}
.contact-row svg{flex:none}
.socials{position:absolute;left:34px;top:210px;display:flex;gap:9px}
.social{width:32px;height:32px;border-radius:4px;background:#e6edf5;color:var(--panel);font-size:7px;display:flex;align-items:center;justify-content:center;font-family:var(--body)}

/* action band */
.band{left:0;top:1053px;width:1143px;height:102px;background:linear-gradient(#bdbdbd,#a2a2a2)}
.badge{width:80px;height:80px;border-radius:50%;background:radial-gradient(circle at 50% 35%,#2ab0bd,#0c6f7e 60%,#07434d);border:5px solid #d9d9d9;display:flex;align-items:center;justify-content:center;text-align:center;font-family:var(--ui);font-weight:500;font-size:12px;line-height:13px;color:var(--white)}
.cta{width:248px;height:68px;border:2px solid #d6d6d6;background:linear-gradient(#3a3a3a,#0e0e0e 55%,#000);display:flex;align-items:center;justify-content:center;gap:18px;font-family:var(--ui);font-size:24px;color:var(--white)}

.footer{left:0;top:1155px;width:1143px;height:45px;background:linear-gradient(#1a5aa8,#0b3a78);text-align:center;line-height:45px;font-size:11px;color:#e6eef8}
</style>
</head>
<body>
<div class="page">

  <header class="abs header">
    <div class="abs mic" role="img" aria-label="Vintage studio microphone"></div>
    <div class="abs logo">VELMAR<br>Radio</div>
    <div class="abs wordmark">Velmar Radio</div>
    <div class="abs lang-label">Language</div>
    <div class="abs lang-select">
      <svg width="12" height="10" viewBox="0 0 12 10"><path d="M1 1h10L6 9z" fill="#0b3a78"/></svg>
    </div>
  </header>

  <nav class="abs nav">
    <a class="active" href="#">Home</a>
    <a href="#" style="left:280px">About Us</a>
    <a href="#" style="left:396px">Sevices</a>
    <a href="#" style="left:497px">Blog</a>
    <a href="#" style="left:577px">News</a>
    <a href="#" style="left:695px">Downloads</a>
    <a href="#" style="left:851px">Chatterloop Login</a>
    <a href="#" style="left:1008px">Contact Us</a>
  </nav>

  <section class="abs hero"></section>
  <svg class="abs floor" width="1143" height="110" viewBox="0 0 1143 110">
    <path d="M110 8H1030L880 90H260Z" fill="#4f93dc" opacity=".35"/>
    <path d="M190 40H960L850 100H300Z" fill="#0b3a78" opacity=".4"/>
  </svg>
  <div class="abs slide-far-left" role="img" aria-label="Green dancer artwork slide"></div>
  <div class="abs slide-side slide-left" role="img" aria-label="Speaker slide"></div>
  <div class="abs slide-side slide-right" role="img" aria-label="Speaker slide"></div>
  <div class="abs slide-far-right" role="img" aria-label="White artwork slide"></div>
  <div class="abs slide-main" role="img" aria-label="Black and white photo of a smiling listener enjoying music"></div>
  <svg class="abs arrow" style="left:72px" width="20" height="28" viewBox="0 0 20 28"><path d="M16 2L4 14l12 12" fill="none" stroke="#c9d3de" stroke-width="3"/></svg>
  <svg class="abs arrow" style="left:1044px;top:467px" width="20" height="28" viewBox="0 0 20 28"><path d="M4 2l12 12L4 26" fill="none" stroke="#c9d3de" stroke-width="3"/></svg>

  <!-- login -->
  <div class="abs panel-tab login-tab"></div>
  <section class="abs panel login">
    <h2>Login</h2>
    <span class="field-label" style="top:68px">User Name</span>
    <div class="field" style="top:95px"></div>
    <span class="field-label" style="top:128px">Password</span>
    <div class="field" style="top:155px"></div>
    <div class="sign-in">Sign In</div>
    <div class="forgot">Forgot Password ?</div>
  </section>

  <!-- now playing -->
  <h2 class="abs section-title" style="left:297px;top:726px">Now playing</h2>
  <div class="abs player">
    <div class="player-screen">
      <div class="player-title">Turn it Up</div>
      <svg class="abs" style="left:60px;top:84px" width="143" height="34" viewBox="0 0 143 34">
        <rect x="0" y="8" width="143" height="18" rx="9" fill="#222" stroke="#555"/>
        <path d="M22 12v10M34 12l-10 5 10 5z" fill="#5b8fe0" stroke="#5b8fe0"/>
        <path d="M121 12v10M109 12l10 5-10 5z" fill="#5b8fe0" stroke="#5b8fe0"/>
        <circle cx="71" cy="17" r="16" fill="#2d6fd8" stroke="#9ec2f5" stroke-width="2"/>
        <path d="M66 9l12 8-12 8z" fill="#fff"/>
      </svg>
      <div class="player-foot">Stream Player 11</div>
    </div>
    <svg class="abs" style="left:216px;top:176px" width="18" height="42" viewBox="0 0 18 42"><rect x="1" y="1" width="16" height="40" rx="3" fill="#ddd"/><rect x="7" y="14" width="4" height="24" fill="#3b7fe0"/></svg>
  </div>
  <svg class="abs player-bar" width="283" height="16" viewBox="0 0 283 16">
    <rect x="2" y="1" width="18" height="13" rx="2" fill="#e5e5e5" stroke="#999"/><path d="M9 4l6 3.5-6 3.5z" fill="#333"/>
    <rect x="32" y="5" width="136" height="5" rx="2" fill="#555"/><rect x="32" y="5" width="80" height="5" rx="2" fill="#3b7fe0"/>
    <circle cx="64" cy="7.5" r="4" fill="#ddd"/>
    <text x="172" y="11" font-size="6" fill="#666" font-family="Arimo,sans-serif">1:47 / 12:35</text>
    <rect x="218" y="1" width="16" height="13" rx="2" fill="#e5e5e5" stroke="#999"/>
    <rect x="238" y="1" width="16" height="13" rx="2" fill="#e5e5e5" stroke="#999"/>
    <rect x="259" y="1" width="16" height="13" rx="2" fill="#e5e5e5" stroke="#999"/>
  </svg>

  <!-- events -->
  <h2 class="abs section-title" style="left:617px;top:726px">Up Coming Events</h2>
  <article class="abs event" style="top:777px">
    <div class="event-thumb" role="img" aria-label="DJ with headphones"></div>
    <span class="event-name">Name Here</span><span class="event-more">more</span>
    <p class="event-text">Lorem Ipsum is simply dummy text of the printing and typesetting</p>
  </article>
  <article class="abs event" style="top:848px">
    <div class="event-thumb" role="img" aria-label="DJ with headphones"></div>
    <span class="event-name">Name Here</span><span class="event-more">more</span>
    <p class="event-text">Lorem Ipsum is simply dummy text of the printing and typesetting</p>
  </article>
  <article class="abs event" style="top:919px">
    <div class="event-thumb" role="img" aria-label="DJ with headphones"></div>
    <span class="event-name">Name Here</span><span class="event-more">more</span>
    <p class="event-text">Lorem Ipsum is simply dummy text of the printing and typesetting</p>
  </article>

  <!-- contact -->
  <div class="abs panel-tab contact-tab"></div>
  <section class="abs panel contact">
    <h3 style="top:34px">CONTACT ME</h3>
    <div class="contact-row" style="top:63px">
      <svg width="20" height="14" viewBox="0 0 20 14"><rect x="1" y="1" width="18" height="12" fill="#dfe6ef"/><path d="M1 1l9 7 9-7" fill="none" stroke="#0b3a78" stroke-width="1.3"/></svg>
      info@velmarmail.com</div>
    <div class="contact-row" style="top:93px">
      <svg width="20" height="16" viewBox="0 0 20 16"><path d="M4 1c-3 2-2 7 2 11s8 4 9 2l-3-3-2 1c-2-1-3-3-4-4l1-2z" fill="#dfe6ef"/></svg>
      555-014-7890</div>
    <div class="contact-row" style="top:123px">
      <svg width="20" height="16" viewBox="0 0 20 16"><rect x="4" y="1" width="12" height="14" fill="#dfe6ef"/><path d="M10 3v8M6.5 8l3.5 3.5L13.5 8" fill="none" stroke="#0b3a78" stroke-width="1.6"/></svg>
      Download My CV</div>
    <h3 style="top:184px">CONNECT WITH ME</h3>
    <div class="socials">
      <span class="social">Chirp</span>
      <span class="social" style="font-size:5px">Chatterloop</span>
      <span class="social">Linkly</span>
      <span class="social">Snapr</span>
      <span class="social">Artly</span>
    </div>
  </section>

  <!-- action band -->
  <section class="abs band"></section>
  <div class="abs badge" style="left:21px;top:1068px">REQUEST<br>A<br>SONG</div>
  <div class="abs cta" style="left:118px;top:1075px">
    <svg width="22" height="16" viewBox="0 0 22 16"><path d="M0 0l11 8-11 8zM11 0l11 8-11 8z" fill="#fff"/></svg>Click Here<svg width="22" height="16" viewBox="0 0 22 16"><path d="M22 0L11 8l11 8zM11 0L0 8l11 8z" fill="#fff"/></svg></div>
  <div class="abs badge" style="left:401px;top:1068px">SEND<br>PAGE TO<br>FRIEND</div>
  <div class="abs cta" style="left:501px;top:1075px">
    <svg width="22" height="16" viewBox="0 0 22 16"><path d="M0 0l11 8-11 8zM11 0l11 8-11 8z" fill="#fff"/></svg>Click Here<svg width="22" height="16" viewBox="0 0 22 16"><path d="M22 0L11 8l11 8zM11 0L0 8l11 8z" fill="#fff"/></svg></div>
  <div class="abs badge" style="left:782px;top:1068px">CHAT<br>ROOM</div>
  <div class="abs cta" style="left:881px;top:1075px">
    <svg width="22" height="16" viewBox="0 0 22 16"><path d="M0 0l11 8-11 8zM11 0l11 8-11 8z" fill="#fff"/></svg>Click Here<svg width="22" height="16" viewBox="0 0 22 16"><path d="M22 0L11 8l11 8zM11 0L0 8l11 8z" fill="#fff"/></svg></div>

  <footer class="abs footer">Copyright©2011.www.velmarradio.com</footer>
</div>
</body>
</html>
```